Website design for legal tech start up in Switzerland (B2B)

We are for a legal tech start up in Switzerland called KOVA. We have been running since August 2016. This will be our first live website.

We need a website designed and business card design for our start-up in Switzerland. We also need the Web design to be converted into HTML and CSS files.

Function of website:
• To inform potential customers of our services
• Form a key part of our digital marketing and sales footprint.
• Branding

Please find attached logo.
Updates

Project Deadline Extended Reason: Giving us time to review submissions and provide opportunity for more submissions. Added Thursday, February 16, 2017

Project Deadline Extended
Reason: Looking for more idea's not necessarily set on blue and grey colours only.

Target Market(s)

B2B tech powered legal services.

Industry/Entity Type

Legal

Contact Information for Business Card

Lean and slick design.

Coding

Coded - Design and coding required

Number of Pages Required

5+ page

Requirements
Must have
• VERY LEAN AND CLEAN DESIGN!
• We have received many great standard designs, but we are looking for something more out-of-the box: You can get inspiration from these designs: http://www.pixelvane.com/websites/clean/
• Thanks!!
• Easy content management system
• Well structured coding for additional development
• Responsive webpage for all types of devices
• SEO optimized
• Tabs (Home, services, team, careers, blog, contact us)
• Colour scheme complementary to logo
Nice to have
• Look and Design - Approachable, High-tech, Modern
• Easy to add chat bot capability in future
Should not have
• Too busy/ too much clutter
• Not take to long to load

```html
<!DOCTYPE html>
<html lang="en">
<head>
<meta charset="utf-8">
<title>KOVA — Legal Services</title>
<link rel="stylesheet" href="https://fonts.googleapis.com/css2?family=Mulish:wght@400;600;700&family=Open+Sans:wght@400;600&family=Roboto+Condensed:wght@400&display=swap">
<style>
:root{
  --navy:#1b3a6b;
  --navy-soft:#2c4f84;
  --tab-active:#3f86c6;
  --ink:#3c3c3c;
  --text:#5a5a5a;
  --panel:#f7f7f7;
  --card:#f1f1f1;
  --line:#d9d9d9;
  --icon:#555555;
  --link:#2a7fd0;
  --white:#ffffff;
}
*{margin:0;padding:0;box-sizing:border-box}
html,body{width:1200px;height:2456px;overflow:hidden;background:var(--white)}
body{position:relative;font-family:"Open Sans",Arial,sans-serif;color:var(--text)}
.abs{position:absolute}
.heading{font-family:"Mulish",Arial,sans-serif}
.condensed{font-family:"Roboto Condensed","Arial Narrow",sans-serif}

/* top bar */
.topbar{left:0;top:0;width:1200px;height:39px;background:var(--navy);color:var(--white);font-size:12px}
.topbar span{position:absolute;top:11px;display:flex;align-items:center;gap:8px}

/* header */
.brand{left:96px;top:54px;font-family:"Mulish",Arial,sans-serif;font-weight:700;font-size:110px;line-height:1;color:var(--ink);letter-spacing:5px}
.consult{left:841px;top:61px;width:259px;height:37px;background:var(--navy);color:var(--white);font-family:"Mulish",sans-serif;font-size:15px;display:flex;align-items:center;justify-content:center}
.consult::after{content:"";position:absolute;inset:4px;border:1px dashed rgba(255,255,255,.8)}
.nav{right:100px;top:118px;display:flex;gap:37px;font-family:"Mulish",sans-serif;font-size:16px;color:#333}

/* hero */
.hero{left:0;top:180px;width:1200px;height:491px;overflow:hidden;
  background:
    linear-gradient(180deg,rgba(20,24,36,.35) 0%,rgba(20,24,36,.15) 45%,rgba(10,10,10,.45) 100%),
    radial-gradient(ellipse 40% 30% at 85% 20%,#c98a6a 0%,rgba(201,138,106,0) 100%),
    radial-gradient(ellipse 35% 45% at 55% 55%,#a55a2e 0%,rgba(165,90,46,0) 100%),
    radial-gradient(ellipse 30% 50% at 10% 50%,#8a6a5a 0%,rgba(138,106,90,0) 100%),
    linear-gradient(180deg,#4a5e86 0%,#6d6f86 25%,#7a5a44 50%,#4c3a26 75%,#2c2a22 100%)}
.hero h1{position:absolute;left:0;width:1200px;top:184px;text-align:center;font-family:"Mulish",sans-serif;font-weight:600;font-size:46px;color:var(--white)}
.btn{position:absolute;top:293px;height:51px;display:flex;align-items:center;justify-content:center;font-family:"Mulish",sans-serif;font-size:22px;font-weight:600;color:var(--white)}
.btn-solid{left:426px;width:150px;background:var(--navy)}
.btn-outline{left:612px;width:166px;border:2px solid var(--white)}
.dots{position:absolute;left:548px;top:461px;display:flex;gap:7px}
.dots i{width:13px;height:13px;border-radius:50%;background:var(--white)}
.dots i:first-child{background:var(--navy)}

/* welcome */
.welcome-photo{left:98px;top:737px;width:491px;height:327px;
  background:
    radial-gradient(ellipse 45% 40% at 55% 60%,#f3e3c4 0%,rgba(243,227,196,0) 100%),
    radial-gradient(ellipse 40% 30% at 20% 8%,#ffffff 0%,rgba(255,255,255,0) 100%),
    linear-gradient(180deg,#7fb4de 0%,#bcd8ea 30%,#f1eab0 55%,#e6d7b3 75%,#b7cfe2 100%)}
.welcome h2{position:absolute;left:647px;top:787px;font-size:36px;font-weight:600;color:var(--navy)}
.copy{font-size:12.3px;line-height:21px;text-align:justify;color:var(--text)}
.welcome .p1{left:647px;top:855px;width:455px}
.welcome .p2{left:647px;top:980px;width:455px}

/* practice tabs */
.practice{left:0;top:1121px;width:600px;height:396px;background:var(--panel)}
.tabs{position:absolute;left:0;top:0;width:600px;height:59px;display:flex;background:var(--navy);color:var(--white);font-size:20px}
.tab{display:flex;align-items:center;justify-content:center;height:59px}
.tab.family{width:234px;justify-content:flex-start;padding-left:98px}
.tab.criminal{width:139px;background:var(--tab-active)}
.tab.property{width:227px}
.practice h3{position:absolute;left:98px;top:120px;font-size:38px;font-weight:400;color:var(--navy)}
.practice .p1{left:98px;top:182px;width:472px}
.practice .p2{left:98px;top:264px;width:472px}
.practice a{color:#333;text-decoration:underline}
.practice-photo{left:600px;top:1121px;width:600px;height:396px;
  background:
    radial-gradient(ellipse 30% 35% at 45% 35%,#8a6a52 0%,rgba(138,106,82,0) 100%),
    radial-gradient(ellipse 25% 25% at 75% 55%,#6b5442 0%,rgba(107,84,66,0) 100%),
    linear-gradient(90deg,#1a1816 0%,#2e2824 20%,#3a302a 50%,#221e1b 80%,#0e0d0c 100%)}

/* team */
.team-title{left:0;width:1200px;top:1567px;text-align:center;font-size:34px;font-weight:600;color:var(--navy)}
.card{top:1662px;width:300px;height:384px;background:var(--card);border:1px solid var(--line)}
.card .portrait{position:absolute;left:-1px;top:-1px;width:300px;height:200px}
.card .name{position:absolute;left:54px;top:168px;width:192px;height:59px;background:var(--navy);color:var(--white);font-family:"Mulish",sans-serif;font-weight:600;font-size:25px;display:flex;align-items:center;justify-content:center}
.card .bio{position:absolute;left:17px;top:248px;width:266px;font-size:11.6px;line-height:20.5px;text-align:justify;text-align-last:center;color:var(--text)}
.card .social{position:absolute;left:0;width:298px;top:346px;display:flex;justify-content:center;gap:18px}
.card .social i{width:10px;height:10px;border:1.5px solid var(--icon);border-radius:2px}
.portrait.p-mira{background:
  radial-gradient(ellipse 30% 45% at 50% 55%,#e2b89a 0%,rgba(226,184,154,0) 100%),
  linear-gradient(90deg,#4a3526 0%,#7a5640 35%,#7a5640 65%,#4a3526 100%)}
.portrait.p-tobias{background:
  radial-gradient(ellipse 32% 45% at 52% 55%,#d9a288 0%,rgba(217,162,136,0) 100%),
  linear-gradient(180deg,#7a5636 0%,#9a6e48 60%,#5a4a44 100%)}
.portrait.p-lukas{background:
  radial-gradient(ellipse 25% 35% at 55% 40%,#e2c0a6 0%,rgba(226,192,166,0) 100%),
  linear-gradient(180deg,rgba(0,0,0,0) 55%,#23314d 80%,#1d2a44 100%),
  linear-gradient(90deg,#9aa8a2 0%,#c9cfc8 30%,#6c7674 100%)}

/* footer */
.footer{left:0;top:2117px;width:1200px;height:339px;background:var(--navy);color:var(--white)}
.footer .brand-foot{position:absolute;left:96px;top:84px;font-family:"Mulish",sans-serif;font-weight:700;font-size:68px;line-height:1;letter-spacing:4px}
.footer .follow{position:absolute;left:101px;top:180px;display:flex;gap:33px}
.footer .follow i{width:19px;height:19px;border:2px solid var(--white);border-radius:4px}
.footer h4{position:absolute;top:60px;font-family:"Open Sans",sans-serif;font-size:19px;font-weight:400}
.contact-line{position:absolute;left:363px;display:flex;align-items:center;gap:16px;font-size:14px;font-weight:600}
.contact-line svg{width:16px;height:16px}
.sitemap{position:absolute;left:671px;top:112px;list-style:none;font-size:14px;font-weight:600;line-height:26.7px}
.news-input{position:absolute;left:823px;top:111px;width:238px;height:33px;background:var(--navy-soft);color:#c7d2e3;font-size:13px;display:flex;align-items:center;padding-left:10px}
.news-btn{position:absolute;left:1061px;top:111px;width:39px;height:33px;background:var(--white);display:flex;align-items:center;justify-content:center}
.news-note{position:absolute;left:823px;top:158px;font-size:12.5px}
.rule{position:absolute;left:98px;top:284px;width:1002px;border-top:1px dashed rgba(255,255,255,.45)}
.copyright{position:absolute;left:0;width:1146px;top:306px;text-align:center;font-size:11px;font-weight:600}
</style>
</head>
<body>

<header>
  <div class="abs topbar">
    <span style="left:98px">
      <svg width="10" height="14" viewBox="0 0 10 14"><circle cx="5" cy="4.5" r="4" fill="#fff"/><rect x="4.2" y="7" width="1.6" height="7" fill="#fff"/></svg>
      14 Linden Lane , Switzerland
    </span>
    <span style="left:848px">
      <svg width="13" height="13" viewBox="0 0 24 24"><path fill="#fff" d="M6.6 10.8a15 15 0 0 0 6.6 6.6l2.2-2.2a1 1 0 0 1 1-.25 11.4 11.4 0 0 0 3.6.57 1 1 0 0 1 1 1V20a1 1 0 0 1-1 1A17 17 0 0 1 3 4a1 1 0 0 1 1-1h3.5a1 1 0 0 1 1 1c0 1.25.2 2.45.57 3.57a1 1 0 0 1-.25 1z"/></svg>
      256 0142 3370
    </span>
    <span style="left:985px">
      <svg width="11" height="13" viewBox="0 0 11 13"><rect x="0" y="5.5" width="11" height="7.5" rx="1" fill="#fff"/><path d="M2.5 5.5V4a3 3 0 0 1 6 0v1.5" stroke="#fff" stroke-width="1.6" fill="none"/></svg>
      Sign in / Sign Up
    </span>
  </div>

  <div class="abs brand">KOVA</div>
  <div class="abs consult">Get Free Consultation</div>
  <nav class="abs nav">
    <span>Home</span><span>Our Services</span><span>Team</span><span>Careers</span><span>Blog</span><span>Contact Us</span>
  </nav>
</header>

<section class="abs hero" role="img" aria-label="Evening view of an old Swiss town with church spires above a river">
  <h1>Get All Your Problem Solved Here</h1>
  <div class="btn btn-solid">Read More</div>
  <div class="btn btn-outline">Contact Us</div>
  <div class="dots"><i></i><i></i><i></i><i></i></div>
</section>

<section class="welcome">
  <div class="abs welcome-photo" role="img" aria-label="Smiling family of four outdoors under a bright sky"></div>
  <h2 class="heading">Welcome To KOVA</h2>
  <p class="abs copy p1">Lorem Ipsum has been the industry's standard dummy text ever since the 1500s, when an unknown printer took a galley of type and scrambled it to make a type specimen book. It has survived not only five centuries, but also the leap into electronic typesetting, remaining essentially unchanged. It was popularised in the 1960s.</p>
  <p class="abs copy p2">Lorem Ipsum has been the industry's standard dummy text ever since the 1500s, when an unknown printer took a galley.</p>
</section>

<section class="abs practice">
  <div class="tabs condensed">
    <div class="tab family">Family</div>
    <div class="tab criminal">Criminal</div>
    <div class="tab property">Property Case</div>
  </div>
  <h3 class="condensed">Criminal</h3>
  <p class="abs copy p1">Lorem Ipsum has been the industry's standard dummy text ever since the 1500s, when an unknown printer took a galley of type and scrambled it to make a type specimen book. It has survived not only five centuries.</p>
  <p class="abs copy p2">Lorem Ipsum has been the industry's standard dummy text ever since the 1500s, when an unknown printer took a galley of type and scrambled it to make a type specimen book. It has survived not only five centuries. <a>Read More</a></p>
</section>
<div class="abs practice-photo" role="img" aria-label="Handcuffed hand gripping prison bars in dim light"></div>

<section class="team">
  <h2 class="abs heading team-title">Our Team</h2>

  <article class="abs card" style="left:98px">
    <div class="portrait p-mira" role="img" aria-label="Portrait of team member Mira"></div>
    <div class="name">Mira</div>
    <p class="bio">Lorem Ipsum has been the industry's standard dummy text ever since the 1500s, when an unknown printer took a galley of type and scrambled it to make a type specimen book. It</p>
    <div class="social"><i></i><i></i><i></i></div>
  </article>

  <article class="abs card" style="left:450px">
    <div class="portrait p-tobias" role="img" aria-label="Portrait of team member Tobias"></div>
    <div class="name">Tobias</div>
    <p class="bio">Lorem Ipsum has been the industry's standard dummy text ever since the 1500s, when an unknown printer took a galley of type and scrambled it to make a type specimen book. It</p>
    <div class="social"><i></i><i></i><i></i></div>
  </article>

  <article class="abs card" style="left:800px">
    <div class="portrait p-lukas" role="img" aria-label="Portrait of team member Lukas"></div>
    <div class="name">Lukas</div>
    <p class="bio">Lorem Ipsum has been the industry's standard dummy text ever since the 1500s, when an unknown printer took a galley of type and scrambled it to make a type specimen book. It</p>
    <div class="social"><i></i><i></i><i></i></div>
  </article>
</section>

<footer class="abs footer">
  <div class="brand-foot">KOVA</div>
  <div class="follow"><i></i><i></i><i></i><i></i></div>

  <h4 style="left:363px">Contact US</h4>
  <div class="contact-line" style="top:104px">
    <svg viewBox="0 0 10 14"><circle cx="5" cy="4.5" r="4" fill="#fff"/><rect x="4.2" y="7" width="1.6" height="7" fill="#fff"/></svg>
    9 Harbor Road, Switzerland
  </div>
  <div class="contact-line" style="top:138px">
    <svg viewBox="0 0 16 16"><rect width="16" height="16" rx="3" fill="#fff"/><path fill="#1b3a6b" d="M4.5 6.5a7 7 0 0 0 5 5l1.3-1.3 2 1-.6 1.8A8.5 8.5 0 0 1 3 4.5l1.8-.6 1 2z"/></svg>
    +256 0178 4412
  </div>
  <div class="contact-line" style="top:172px">
    <svg viewBox="0 0 16 16"><rect y="3" width="16" height="11" rx="1.5" fill="#fff"/><path d="M1 4l7 5 7-5" stroke="#1b3a6b" stroke-width="1.5" fill="none"/></svg>
    hello@kova-legal.ch
  </div>

  <h4 style="left:671px">Site Map</h4>
  <ul class="sitemap">
    <li>Home</li><li>About Us</li><li>Team</li><li>Clients</li><li>Services</li>
  </ul>

  <h4 style="left:823px">Newsletter</h4>
  <div class="news-input">enter your email</div>
  <div class="news-btn">
    <svg width="16" height="14" viewBox="0 0 16 14"><path d="M1 7h12M8 2l5 5-5 5" stroke="#2a7fd0" stroke-width="2.4" fill="none"/></svg>
  </div>
  <p class="news-note">subscribe our latest news, offes and discounts</p>

  <div class="rule"></div>
  <p class="copyright">Copyrights © 2017 &nbsp;Kova .All Rights Reserved</p>
</footer>

</body>
</html>
```